Dovecote Realty

Business cards for 4 people

They need to say for all
87 Tarrow Quay, Boston MA 02114

Each person will have their own personal information
We would like gold embossing for the name of the company
Marla is the blonde sitting in the chair smiling her information should be on the back of the card with her name and information
Should say for slogan classic pattern, elevated experience
grace@dovecoteprops.com
(413) 555-0182

Odette is the brunette with wavy hair in the tan suit odette@dovecoteprops.com
(617) 555-0137

faith@dovecoteprops.com
(413) 555-0164
standing next to the chair

hope@dovecoteprops.com
(413) 555-0199
close up headshot

```html
<!DOCTYPE html>
<html lang="en">
<head>
<meta charset="utf-8">
<title>Dovecote Realty – Business Cards</title>
<link href="https://fonts.googleapis.com/css2?family=Open+Sans:wght@400;600;700&display=swap" rel="stylesheet">
<style>
  :root {
    --backdrop: #222222;
    --card: #1b1b1c;
    --card-front: #1d1e21;
    --gold: #e9b45c;
    --emboss: #3a3b40;
    --text-light: #f2f2f2;
    --photo-dark: #2a211b;
    --photo-warm: #8a5f3e;
  }
  * { margin: 0; padding: 0; box-sizing: border-box; }
  html, body {
    width: 1200px; height: 780px; overflow: hidden;
    background: var(--backdrop);
    font-family: "Open Sans", Arial, sans-serif;
  }
  .canvas { position: relative; width: 1200px; height: 780px; }

  .card {
    position: absolute;
    width: 540px; height: 310px;
    border-radius: 4px;
    overflow: hidden;
    box-shadow: 0 18px 40px rgba(0,0,0,.45);
  }

  /* Contact side */
  .card--contact { left: 40px; top: 235px; background: var(--card); }
  .portrait {
    position: absolute; left: 18px; top: 26px;
    width: 210px; height: 230px;
    border-radius: 90px 90px 6px 6px;
    background: radial-gradient(ellipse at 50% 35%, var(--photo-warm) 0%, #6b4630 45%, var(--photo-dark) 100%);
  }
  .bottom-band {
    position: absolute; left: 0; bottom: 0; width: 100%; height: 18px;
  }
  .side-tab {
    position: absolute; right: 0; top: 168px; width: 14px; height: 34px;
    background: var(--gold);
  }
  .brand {
    position: absolute; right: 40px; top: 28px;
    display: flex; align-items: center; gap: 12px;
  }
  .brand__name {
    font-weight: 600; font-size: 22px; letter-spacing: 3px;
    text-transform: uppercase; color: var(--gold);
    text-align: right; line-height: 1.15;
  }
  .brand__mark {
    width: 54px; height: 54px; border-radius: 50%;
    border: 3px solid var(--gold);
  }
  .person {
    position: absolute; right: 40px; top: 110px; text-align: right;
  }
  .person__name {
    font-weight: 700; font-size: 30px; color: var(--gold); line-height: 1.1;
  }
  .person__title {
    font-size: 11px; color: var(--text-light); margin-top: 2px;
  }
  .address {
    position: absolute; right: 40px; top: 178px; text-align: right;
    font-size: 14px; color: var(--text-light); line-height: 1.3;
  }
  .contact-list {
    position: absolute; right: 40px; top: 222px; list-style: none;
    font-size: 13px; color: var(--text-light);
  }
  .contact-list li {
    display: flex; justify-content: flex-end; align-items: center;
    gap: 8px; line-height: 19px;
  }
  .contact-list svg { width: 12px; height: 12px; fill: none; stroke: var(--gold); stroke-width: 2; }

  /* Brand side */
  .card--brand { left: 620px; top: 235px; background: var(--card-front); }
  .brand-emboss {
    position: absolute; inset: 0;
    display: flex; align-items: center; justify-content: center; gap: 18px;
  }
  .brand-emboss__name {
    font-weight: 600; font-size: 34px; letter-spacing: 5px;
    text-transform: uppercase; color: var(--emboss); text-align: center; line-height: 1.2;
  }
  .brand-emboss__mark {
    width: 96px; height: 96px; border-radius: 50%;
    border: 3px solid var(--emboss);
  }
</style>
</head>
<body>
<main class="canvas">

  <section class="card card--contact" aria-label="Contact side of business card">
    <div class="portrait" role="img" aria-label="Portrait photo of Odette Renaud in a tan suit"></div>
    <svg class="bottom-band" viewBox="0 0 540 18" preserveAspectRatio="none" aria-hidden="true">
      <polygon points="0,0 250,0 262,10 540,10 540,18 0,18" fill="#e9b45c"/>
    </svg>
    <div class="side-tab" aria-hidden="true"></div>

    <div class="brand">
      <div class="brand__name">Dovecote<br>Realty</div>
      <div class="brand__mark" aria-hidden="true"></div>
    </div>

    <div class="person">
      <h1 class="person__name">Odette Renaud</h1>
      <p class="person__title">Real Estate Advisor and Sales Manager</p>
    </div>

    <p class="address">87 Tarrow Quay,<br>Boston MA 02114</p>

    <ul class="contact-list">
      <li>(617) 555-0137
        <svg viewBox="0 0 12 12" aria-hidden="true"><path d="M3 1l2 2-1 2c1 1 2 2 3 3l2-1 2 2-2 2C5 11 1 7 1 3z"/></svg>
      </li>
      <li>www.dovecoteprops.com
        <svg viewBox="0 0 12 12" aria-hidden="true"><circle cx="6" cy="6" r="5"/><path d="M1 6h10M6 1c2 2 2 8 0 10M6 1c-2 2-2 8 0 10"/></svg>
      </li>
      <li>odette@dovecoteprops.com
        <svg viewBox="0 0 12 12" aria-hidden="true"><rect x="1" y="3" width="10" height="7"/><path d="M1 3l5 4 5-4"/></svg>
      </li>
    </ul>
  </section>

  <section class="card card--brand" aria-label="Brand side of business card">
    <div class="brand-emboss">
      <div class="brand-emboss__name">Dovecote<br>Realty</div>
      <div class="brand-emboss__mark" aria-hidden="true"></div>
    </div>
  </section>

</main>
</body>
</html>
```